Super elegant, crisp & clean Business card design required

We recently upgraded our branding - which is on our website - talvendoraphoto.com

I would like a simple, yet elegant, clean business card design please.

The font of my logo is Cinzel - and because of the natural colour - it's best to have this on a black background.

I would like to have the back of the business card - with simply my logo.

PLEASE DO NOT SUBMIT A COMPLICATED / UNCLEAN DESIGN

Industry/Entity Type

Business

Contact Information for Business Card

Talven Doroshko Photography

Font styles to use
Other font styles liked:
• Cinzel

Requirements
Must have
• A backpage with nothing but my logo
• Simple design - stands out
Should not have
• Colour that dont align with my logo
• Over complicated '/ non symmetrical design

```html
<!DOCTYPE html>
<html lang="en">
<head>
<meta charset="utf-8">
<title>Talven Doroshko Photography — Business Card</title>
<link href="https://fonts.googleapis.com/css2?family=Cinzel:wght@400;700&family=Open+Sans:wght@400;600&display=swap" rel="stylesheet">
<style>
  :root {
    --stage: #e9e6e1;
    --card-black: #000000;
    --card-khaki: #857a5e;
    --gold: #8f7d5a;
    --white: #ffffff;
    --ink: #111111;
  }
  * { margin: 0; padding: 0; box-sizing: border-box; }
  html, body { width: 1200px; height: 900px; overflow: hidden; }
  body { background: var(--stage); position: relative; }

  .card { position: absolute; text-align: center; }

  .card--front {
    left: 78px; top: 34px; width: 588px; height: 364px;
    background: var(--card-black);
    color: var(--white);
    font-family: "Open Sans", sans-serif;
  }
  .brand-name {
    position: absolute; left: 0; right: 0; top: 82px;
    font-family: "Cinzel", serif; font-weight: 400;
    font-size: 38px; letter-spacing: 1px; color: var(--gold);
    line-height: 1;
  }
  .brand-tagline {
    position: absolute; left: 0; right: 0; top: 130px;
    font-family: "Cinzel", serif; font-weight: 400;
    font-size: 18px; letter-spacing: 10px; color: var(--gold);
    line-height: 1;
  }
  .contact-block { position: absolute; left: 0; right: 0; top: 180px; }
  .person-name {
    font-family: "Cinzel", serif; font-weight: 700;
    font-size: 20px; color: var(--gold); line-height: 1.1;
  }
  .person-role { font-size: 15px; line-height: 1.3; }
  .contact-list { list-style: none; margin-top: 17px; font-size: 15px; line-height: 22px; }
  .contact-label { color: var(--gold); font-weight: 600; }
  .address { position: absolute; left: 0; right: 0; top: 337px; font-size: 15px; }

  .card--back {
    left: 388px; top: 505px; width: 566px; height: 352px;
    background: var(--card-khaki);
    color: var(--ink);
  }
  .mark-dot {
    position: absolute; left: 253px; top: 108px;
    width: 60px; height: 60px; border: 2px solid var(--ink); border-radius: 50%;
  }
  .back-name {
    position: absolute; left: 0; right: 0; top: 237px;
    font-family: "Cinzel", serif; font-weight: 400; color: var(--ink);
    line-height: 1;
  }
  .back-name .line-main { display: block; font-size: 27px; letter-spacing: 0.5px; }
  .back-name .line-sub { display: block; font-size: 12px; letter-spacing: 7px; margin-top: 5px; }
  .website {
    position: absolute; left: 0; right: 0; top: 283px;
    font-family: "Open Sans", sans-serif; font-size: 15px; color: var(--ink);
  }
</style>
</head>
<body>
  <section class="card card--front" aria-label="Business card front">
    <h1 class="brand-name">Talven Doroshko</h1>
    <p class="brand-tagline">Photography</p>
    <div class="contact-block">
      <p class="person-name">MAREK ELLISON</p>
      <p class="person-role">Managing Director</p>
      <ul class="contact-list">
        <li><span class="contact-label">P:</span> 555-218-4630</li>
        <li><span class="contact-label">F:</span> 555-218-4630</li>
        <li><span class="contact-label">E:</span> hello@talvendoraphoto.com</li>
      </ul>
    </div>
    <p class="address">1234, Address Goes HereCountry Name, 123456</p>
  </section>

  <section class="card card--back" aria-label="Business card back">
    <span class="mark-dot"></span>
    <p class="back-name">
      <span class="line-main">Talven Doroshko</span>
      <span class="line-sub">Photography</span>
    </p>
    <p class="website">www.talvendoraphoto.com</p>
  </section>
</body>
</html>
```